Signage Design Project - For Sale and For Rent

I am looking to revamp our For Sale and For Rent signboards.
The size of the board is
1250mm WIDTH
1800mm HEIGHT
The board is one sided, and slightly curved (will not impact the design at all)
For Rent Signs need to include the following information;
NESTor Logo
For Rent
Website
Social link (www.social.example/nestorhomesco)
Phone number 6148 7309
For Sale signs need to include the following information
NESTor logo
For Sale
Website
Social link
Phone number 6148 7309
One signboard with Colin Partridge (this is the agents name)
One signboard with Peter Halvey (this is the agents name)
Full service real estate for a low $5,950 (+GST)
The more bold, punch and creative the better- we are very much an innovative and young company. I would suggest visiting our website, www.nestorhomes.example.au and our facebook page to get a feel for our company.
Updates
Existing signboard + logo files have been updated.
Have also guaranteed payment.
Real Estate

```html
<!DOCTYPE html>
<html lang="en">
<head>
<meta charset="utf-8">
<title>NESTor Property – For Rent Signboard</title>
<link rel="stylesheet" href="https://fonts.googleapis.com/css2?family=League+Gothic&family=Montserrat:wght@600&display=swap">
<style>
  :root {
    --backdrop: #ececec;
    --sky: #e9f0e4;
    --sky-line: #dde8d6;
    --skyline: #a9c49a;
    --brand-green: #6a9a55;
    --web-green: #7ba56a;
    --ink: #111111;
    --paper: #ffffff;
  }
  html, body {
    margin: 0;
    padding: 0;
    width: 1026px;
    height: 1200px;
    overflow: hidden;
    background: var(--backdrop);
  }
  .signboard {
    position: absolute;
    left: 107px;
    top: 15px;
    width: 812px;
    height: 1169px;
    display: block;
  }
  .headline {
    font-family: "League Gothic", "Oswald", sans-serif;
  }
  .label {
    font-family: "Montserrat", sans-serif;
    font-weight: 600;
  }
  .brand-name { fill: var(--ink); font-size: 40px; letter-spacing: 4px; }
  .headline-word { fill: var(--ink); }
  .web-address { fill: var(--web-green); }
  .phone-number { fill: var(--paper); }
  .social-link { fill: var(--paper); font-size: 22px; letter-spacing: 0.5px; }
</style>
</head>
<body>
<svg class="signboard" viewBox="0 0 812 1169" xmlns="http://www.w3.org/2000/svg" role="img" aria-label="NESTor Property for rent signboard">
  <defs>
    <pattern id="sky-lines" width="10" height="6" patternUnits="userSpaceOnUse">
      <rect width="10" height="6" fill="var(--sky)"/>
      <rect y="4" width="10" height="1.2" fill="var(--sky-line)"/>
    </pattern>
  </defs>

  <!-- background -->
  <rect class="sky" width="812" height="1169" fill="url(#sky-lines)"/>
  <rect class="skyline-area" x="0" y="690" width="812" height="479" fill="var(--skyline)" role="img" aria-label="Silhouette of a row of rooftops along the lower half of the board"/>

  <!-- brand -->
  <g class="brand">
    <rect class="brand-square" x="97" y="56" width="64" height="64" fill="var(--brand-green)"/>
    <text class="label brand-name" x="190" y="103">NESTOR PROPERTY</text>
  </g>

  <!-- headline -->
  <g class="headline-block">
    <rect class="rule" x="246" y="179" width="323" height="14" fill="var(--ink)"/>
    <text class="headline headline-word" x="246" y="510" font-size="412" textLength="323" lengthAdjust="spacingAndGlyphs">FOR</text>
    <text class="headline headline-word" x="246" y="750" font-size="290" textLength="323" lengthAdjust="spacingAndGlyphs">RENT</text>
    <rect class="rule" x="246" y="771" width="323" height="18" fill="var(--ink)"/>
  </g>

  <!-- contact -->
  <g class="contact-block">
    <text class="headline web-address" x="246" y="872" font-size="66" textLength="323" lengthAdjust="spacingAndGlyphs">NESTORHOMES.EXAMPLE.AU</text>
    <rect class="rule" x="246" y="908" width="323" height="20" fill="var(--paper)"/>
    <text class="headline phone-number" x="246" y="1049" font-size="138" textLength="323" lengthAdjust="spacingAndGlyphs">6148-7309</text>
    <rect class="rule" x="246" y="1065" width="323" height="16" fill="var(--paper)"/>
  </g>

  <!-- social -->
  <g class="social">
    <rect class="social-mark" x="134" y="1100" width="44" height="44" rx="4" fill="var(--paper)"/>
    <text class="label social-link" x="206" y="1131">WWW.SOCIAL.EXAMPLE/NESTORHOMESCO</text>
  </g>
</svg>
</body>
</html>
```